TeaLantern Flyer

I require an A5 sized flyer to be designed that advertised the new flexible workspace of TeaLantern.
should say it is a "Flexible Workspace with EV Charging"
web address is www.tealantern.co.uk
It should show the 3 different types of membership as priced on the website

```html
<!DOCTYPE html>
<html lang="en">
<head>
<meta charset="utf-8">
<title>TeaLantern Flyer</title>
<link href="https://fonts.googleapis.com/css2?family=Saira+Condensed:ital,wght@0,700;0,800;1,700;1,800&family=Montserrat:wght@400;500;600&display=swap" rel="stylesheet">
<style>
  :root {
    --orange: #f39200;
    --charcoal: #2f2f2f;
    --ink: #1e1e1e;
    --paper: #ffffff;
    --line: #d9d9d9;
    --soft: #cfcfcf;
    --backdrop: #ecebe8;
  }
  * { box-sizing: border-box; margin: 0; padding: 0; }
  html, body { width: 1200px; height: 1200px; overflow: hidden; background: var(--backdrop); }
  .flyer {
    position: absolute; left: 197px; top: 30px; width: 806px; height: 1140px;
    background: var(--charcoal); overflow: hidden;
    font-family: "Montserrat", sans-serif; color: var(--paper);
  }
  .flyer-head { position: absolute; left: 0; top: 0; width: 100%; height: 130px; background: var(--paper); }
  .frame-top { position: absolute; top: 22px; height: 1px; background: var(--orange); }
  .frame-side { position: absolute; top: 22px; width: 1px; height: 1090px; background: linear-gradient(var(--orange), var(--soft)); }
  .frame-bottom { position: absolute; top: 1107px; height: 1px; background: var(--soft); }
  .brand {
    position: absolute; left: 0; top: 40px; width: 100%;
    display: flex; justify-content: center; align-items: center; gap: 14px;
  }
  .brand-dot { width: 22px; height: 22px; border-radius: 50%; background: var(--orange); }
  .brand-name {
    font-family: "Saira Condensed", sans-serif; font-weight: 800; font-size: 76px;
    line-height: 1; color: var(--ink); letter-spacing: 0.5px;
  }
  .hero-photo {
    position: absolute; left: 0; top: 130px; width: 100%; height: 620px;
    background:
      linear-gradient(180deg, rgba(47,47,47,0) 55%, var(--charcoal) 100%),
      radial-gradient(ellipse at 45% 65%, #5a4535 0%, #6f6a66 35%, #b7b7b8 70%, #dedfe2 100%);
  }
  .headline {
    position: absolute; left: 0; top: 572px; width: 100%; text-align: center;
    font-family: "Saira Condensed", sans-serif; font-weight: 800; font-style: italic;
    font-size: 70px; line-height: 68px; color: var(--paper);
  }
  .headline .accent { color: var(--orange); }
  .plan {
    position: absolute; border: 1px solid var(--soft); border-radius: 18px;
    padding: 34px 10px 0 10px;
  }
  .plan--day { left: 92px; top: 768px; width: 204px; height: 280px; }
  .plan--light { left: 300px; top: 741px; width: 198px; height: 325px; border-color: var(--orange); padding-top: 44px; }
  .plan--all { left: 508px; top: 760px; width: 206px; height: 296px; }
  .plan-icon {
    position: absolute; left: 50%; top: -16px; transform: translateX(-50%);
    background: var(--charcoal); padding: 0 10px;
  }
  .plan-title {
    font-family: "Saira Condensed", sans-serif; font-weight: 700; font-style: italic;
    font-size: 22px; line-height: 24px; text-align: center; margin-bottom: 10px;
  }
  .plan--light .plan-title { color: var(--orange); font-size: 26px; line-height: 26px; margin-bottom: 22px; }
  .features { list-style: none; }
  .features li {
    display: flex; gap: 6px; font-size: 8.5px; line-height: 10px; margin-bottom: 11px;
    color: #e6e6e6; white-space: nowrap; letter-spacing: -0.1px;
  }
  .plan--light .features li { font-weight: 600; margin-bottom: 13px; letter-spacing: -0.2px; }
  .plan--all .features li { margin-bottom: 8px; }
  .features svg { flex: 0 0 8px; margin-top: 1px; }
  .price { position: absolute; left: 0; bottom: 14px; width: 100%; text-align: center; }
  .price-amount {
    font-family: "Saira Condensed", sans-serif; font-weight: 700; font-style: italic;
    font-size: 19px; line-height: 19px; color: var(--orange);
  }
  .price-note { font-size: 9px; margin-top: 3px; }
  .web-band {
    position: absolute; left: 247px; top: 1090px; width: 314px; height: 36px;
    background: var(--orange); color: var(--paper); font-size: 19px;
    display: flex; align-items: center; justify-content: center; letter-spacing: 0.3px;
  }
</style>
</head>
<body>
<svg width="0" height="0" style="position:absolute">
  <defs>
    <symbol id="tick-box" viewBox="0 0 8 8">
      <rect x="0.5" y="0.5" width="7" height="7" fill="none" stroke="#e6e6e6" stroke-width="0.8"/>
      <path d="M1.8 4.2 L3.4 5.7 L6.4 2.2" fill="none" stroke="#e6e6e6" stroke-width="0.9"/>
    </symbol>
  </defs>
</svg>

<main class="flyer">
  <header class="flyer-head">
    <div class="brand">
      <span class="brand-dot"></span>
      <span class="brand-name">TeaLantern</span>
    </div>
  </header>

  <div class="hero-photo" role="img" aria-label="Photograph of the open-plan workspace with leather Chesterfield sofas, coffee tables, privacy booths and hot desks"></div>

  <div class="frame-top" style="left:130px;width:250px"></div>
  <div class="frame-top" style="left:430px;width:356px"></div>
  <div class="frame-side" style="left:786px"></div>
  <div class="frame-side" style="left:20px;top:40px;height:1068px;background:linear-gradient(var(--soft),var(--soft))"></div>
  <div class="frame-bottom" style="left:20px;width:214px"></div>
  <div class="frame-bottom" style="left:575px;width:212px"></div>

  <h1 class="headline">
    <span class="accent">Flexible</span> Workspace<br>
    with <span class="accent">EV Charging</span>
  </h1>

  <section class="plan plan--day">
    <svg class="plan-icon" width="50" height="26" viewBox="0 0 50 26">
      <rect x="13" y="6" width="24" height="17" rx="1.5" fill="none" stroke="#e6e6e6" stroke-width="1.2"/>
      <path d="M20 6 V3 H30 V6 M13 13 H37" fill="none" stroke="#e6e6e6" stroke-width="1.2"/>
    </svg>
    <h2 class="plan-title">Day Member</h2>
    <ul class="features">
      <li><svg width="8" height="8"><use href="#tick-box"/></svg>Use of Hot Desks &amp; Lounge Areas</li>
      <li><svg width="8" height="8"><use href="#tick-box"/></svg>Secure Wifi</li>
      <li><svg width="8" height="8"><use href="#tick-box"/></svg>Free Tea &amp; Coffee</li>
    </ul>
    <div class="price">
      <div class="price-amount">£25.00 Each visit</div>
      <div class="price-note">Price Inclusive of VAT</div>
    </div>
  </section>

  <section class="plan plan--light">
    <svg class="plan-icon" width="54" height="34" viewBox="0 0 54 34">
      <circle cx="25" cy="19" r="12" fill="none" stroke="#f39200" stroke-width="1.4"/>
      <circle cx="25" cy="19" r="6.5" fill="none" stroke="#f39200" stroke-width="1.4"/>
      <circle cx="25" cy="19" r="1.8" fill="#f39200"/>
      <path d="M25 19 L40 4 M36 3 L41 3 L41 8" fill="none" stroke="#f39200" stroke-width="1.4"/>
    </svg>
    <h2 class="plan-title">Light<br>Member</h2>
    <ul class="features">
      <li><svg width="8" height="8"><use href="#tick-box"/></svg>Use of Hot Desks &amp; Lounge Areas</li>
      <li><svg width="8" height="8"><use href="#tick-box"/></svg>Secure Wifi</li>
      <li><svg width="8" height="8"><use href="#tick-box"/></svg>Free Tea &amp; Coffee</li>
      <li><svg width="8" height="8"><use href="#tick-box"/></svg>Discounted E/V Charge Rates</li>
      <li><svg width="8" height="8"><use href="#tick-box"/></svg>Access to Meeting Rooms<br>(£10+vat per person, per hour)</li>
    </ul>
    <div class="price">
      <div class="price-amount">£18 a month<br>+ £18 Each Visit / month</div>
      <div class="price-note">Price Inclusive of VAT</div>
    </div>
  </section>

  <section class="plan plan--all">
    <svg class="plan-icon" width="52" height="26" viewBox="0 0 52 26">
      <path d="M15 8 L20 3 H32 L37 8 L26 22 Z M15 8 H37 M22 8 L26 22 L30 8 M20 3 L22 8 M32 3 L30 8" fill="none" stroke="#e6e6e6" stroke-width="1.1"/>
    </svg>
    <h2 class="plan-title">All Access Member</h2>
    <ul class="features">
      <li><svg width="8" height="8"><use href="#tick-box"/></svg>Unlimited Number of Visits Each Month</li>
      <li><svg width="8" height="8"><use href="#tick-box"/></svg>Dedicated Desk<br>(lockable draws + £60 a month)</li>
      <li><svg width="8" height="8"><use href="#tick-box"/></svg>Receptionist to Meet &amp; Greet Guests</li>
      <li><svg width="8" height="8"><use href="#tick-box"/></svg>Use of Lounge Areas</li>
      <li><svg width="8" height="8"><use href="#tick-box"/></svg>Secure Wifi</li>
      <li><svg width="8" height="8"><use href="#tick-box"/></svg>Free Tea &amp; Coffee</li>
      <li><svg width="8" height="8"><use href="#tick-box"/></svg>Discounted E/V Charge Rates</li>
      <li><svg width="8" height="8"><use href="#tick-box"/></svg>Access to Meeting Rooms<br>(£10+vat per person, per hour)</li>
    </ul>
    <div class="price">
      <div class="price-amount">£180.00 / month</div>
      <div class="price-note">Price Inclusive of VAT</div>
    </div>
  </section>

  <div class="web-band">www.tealantern.co.uk</div>
</main>
</body>
</html>
```